Business Card: RW Office Partners - Your organised problem solver

Business Name: RW Office Partners
Website: www.rwofficepartners.com.au
Email: marisol@rwofficepartners.com.au
Mobile: 61 482 907 236
Facebook: @rwofficepartners
Instrgram: @rwofficepartners

Brading Colours:
HEX
#986474
#ddccd3
#7a8498
#c9d8e4
#000000
#ffffff

Tag Line: Your calm, capable back office

Link to DRAFT website:
https://deskhelpcollective.wixsite.com/rw-office-partners

About Page from the website:
My name is Marisol Wrenfield, and I would love to assist you to become more productive in your day to day and achieve your business and personal goals.
My mission is to give you time, time to work on the important tasks of your business or to be able to spend more time with your family. I will take on the tasks you don’t have time for, don’t know well or simply don’t like to do.
I have an extensive background in Administration, Tender Coordination, Document Control, WHS and Quality Management working primarily in the Construction, Mining and Corporate World.
I am passionate about being organised, having order and making things in your life (and mine) easier! I love to watch something unfold and grow into something amazing! I am known for being the go-to problem solver, the organiser of all things, producing high standards of work even under pressure. I’m also a confident communicator, and I understand that you’re busy running your business.

Target Market(s)

Small to Medium Business who require assistance in their business by a virtual assistant.

Industry/Entity Type

Virtual Assistant

Contact Information for Business Card

Mobile: 61 482 907 236

Font styles to use
Sans Serif

Colors
ffffff

Requirements
Must have
• Branding Colours as outlined.
Contact Details as outlined.
Logo as provided.
Proper contact details - mobile, facebook, instragm, website.
Simple, Elegant, very clean looking.
Should not have
• Note cute with pictures.
Not too girly as still want to market to construction companies.

```html
<!DOCTYPE html>
<html lang="en">
<head>
<meta charset="utf-8">
<title>RW Office Partners – Business Card</title>
<link rel="stylesheet" href="https://fonts.googleapis.com/css2?family=Montserrat:wght@500;600&family=Roboto:wght@300;400;500&display=swap">
<style>
  :root {
    --backdrop: #e6e6e6;
    --card: #2e2e30;
    --card-edge: #986474;
    --mauve: #986474;
    --mauve-light: #b07f8e;
    --white: #ffffff;
    --soft-white: #e4e4e4;
    --rule: #6a6a6c;
  }
  * { box-sizing: border-box; margin: 0; padding: 0; }
  html, body { width: 1200px; height: 801px; overflow: hidden; }
  body {
    background: var(--backdrop);
    font-family: "Roboto", Arial, sans-serif;
    display: flex;
    align-items: center;
    justify-content: center;
    gap: 40px;
  }
  .card {
    position: relative;
    width: 540px;
    height: 309px;
    background: var(--card);
    border-bottom: 3px solid var(--card-edge);
    box-shadow: 0 6px 18px rgba(0,0,0,0.18);
    overflow: hidden;
  }

  /* Contact side */
  .card-front .brand {
    position: absolute;
    left: 42px;
    top: 138px;
    width: 190px;
    font-family: "Montserrat", Arial, sans-serif;
    font-weight: 600;
    font-size: 21px;
    line-height: 1.1;
    letter-spacing: 0.5px;
    text-transform: uppercase;
    color: var(--white);
  }
  .card-front .divider {
    position: absolute;
    left: 252px;
    top: 52px;
    width: 1px;
    height: 205px;
    background: var(--rule);
  }
  .card-front .details {
    position: absolute;
    left: 276px;
    top: 58px;
    right: 20px;
  }
  .person-name {
    font-size: 19px;
    font-weight: 500;
    color: var(--mauve-light);
  }
  .person-role {
    font-size: 14px;
    font-weight: 300;
    color: var(--white);
    margin-bottom: 16px;
  }
  .contact-list { list-style: none; }
  .contact-list li {
    display: flex;
    align-items: center;
    gap: 9px;
    font-size: 12.5px;
    font-weight: 300;
    color: var(--soft-white);
    line-height: 1.75;
    white-space: nowrap;
  }
  .contact-list svg { width: 11px; height: 11px; flex: none; }
  .contact-list .accent { color: var(--mauve-light); }

  /* Tagline side */
  .card-back .brand {
    position: absolute;
    right: 40px;
    top: 108px;
    width: 300px;
    font-family: "Montserrat", Arial, sans-serif;
    font-weight: 600;
    font-size: 34px;
    line-height: 1.05;
    letter-spacing: 1px;
    text-transform: uppercase;
    color: var(--white);
  }
  .card-back .tagline {
    position: absolute;
    right: 40px;
    top: 200px;
    width: 300px;
    font-size: 15px;
    font-weight: 300;
    color: var(--soft-white);
    letter-spacing: 0.3px;
    white-space: nowrap;
  }
</style>
</head>
<body>

  <section class="card card-front" aria-label="Business card, contact side">
    <div class="brand">RW Office Partners</div>
    <div class="divider"></div>
    <div class="details">
      <p class="person-name">Callum Ashby</p>
      <p class="person-role">Manager</p>
      <ul class="contact-list">
        <li>
          <svg viewBox="0 0 12 12" aria-hidden="true"><rect x="3" y="0.8" width="6" height="10.4" rx="1" fill="none" stroke="var(--mauve-light)" stroke-width="1.1"/><line x1="5" y1="9.4" x2="7" y2="9.4" stroke="var(--mauve-light)" stroke-width="1"/></svg>
          61 482 907 236
        </li>
        <li>
          <svg viewBox="0 0 12 12" aria-hidden="true"><circle cx="6" cy="6" r="5" fill="var(--mauve-light)"/></svg>
          @rwofficepartners
        </li>
        <li>
          <svg viewBox="0 0 12 12" aria-hidden="true"><rect x="1" y="1" width="10" height="10" rx="1.5" fill="var(--mauve-light)"/></svg>
          @rwofficepartners
        </li>
        <li>
          <svg viewBox="0 0 12 12" aria-hidden="true"><rect x="0.8" y="2.5" width="10.4" height="7" fill="none" stroke="var(--mauve-light)" stroke-width="1.1"/><polyline points="0.8,2.5 6,6.6 11.2,2.5" fill="none" stroke="var(--mauve-light)" stroke-width="1.1"/></svg>
          marisol@rwofficepartners.com.au
        </li>
        <li>
          <svg viewBox="0 0 12 12" aria-hidden="true"><circle cx="6" cy="6" r="5" fill="none" stroke="var(--mauve-light)" stroke-width="1.1"/><ellipse cx="6" cy="6" rx="2.2" ry="5" fill="none" stroke="var(--mauve-light)" stroke-width="0.9"/><line x1="1" y1="6" x2="11" y2="6" stroke="var(--mauve-light)" stroke-width="0.9"/></svg>
          <span>www.<span class="accent">rwofficepartners</span>.com.au</span>
        </li>
      </ul>
    </div>
  </section>

  <section class="card card-back" aria-label="Business card, tagline side">
    <h1 class="brand">RW Office Partners</h1>
    <p class="tagline">Your calm, capable back office</p>
  </section>

</body>
</html>
```